Australian small vineyard seeking wine label.

We need a wine label design for a new wine brand \Boutique winery - 2 vintages so far, looking for something a little eye catching, but simple.
Wine label name: Marlow and Fenn
2013 Cabernet Shiraz
2014 Shiraz
Estate grown
Vineyard located at Ashbrook in the Clare valley South Australia.

Target Market(s)

ladies aged between 20 and 50

Industry/Entity Type

Boutique

Logo Text

Marlow and Fenn

Logo styles of interest
Emblem Logo
Pictorial/Combination Logo
Abstract Logo
Character Logo
Font styles to use
Serif
Script

Requirements
Must have
• easy to read text
Nice to have
• The grape grower and winemaker is Peter Hallam -
• had some thoughts of Admiral Thorne - Australian - naval flag
• But very open to ideas
Should not have
• over complications and colors due to cost of wine label being determined by amount of colors required abd print set up.

```html
<!DOCTYPE html>
<html lang="en">
<head>
<meta charset="utf-8">
<title>Marlow and Fenn — Shiraz 2014 Labels</title>
<link href="https://fonts.googleapis.com/css2?family=Cormorant+Garamond:wght@400;500;600&display=swap" rel="stylesheet">
<style>
  :root {
    --backdrop: #d9d9d9;
    --cream: #ece4c8;
    --cream-edge: #ddd3b3;
    --charcoal: #1e1e1e;
    --charcoal-edge: #2a2a2a;
    --wine-red: #9e1b24;
    --ink-dark: #1a1a1a;
    --ink-light: #e6e0cf;
    --sketch-dark: #8d8a80;
    --sketch-light: #5e5e5e;
  }
  * { box-sizing: border-box; margin: 0; padding: 0; }
  html, body {
    width: 1200px;
    height: 800px;
    overflow: hidden;
  }
  body {
    background: var(--backdrop);
    font-family: "Cormorant Garamond", Georgia, serif;
    display: flex;
    align-items: center;
    justify-content: center;
    gap: 60px;
  }
  .label {
    width: 460px;
    height: 360px;
    padding: 30px 32px 26px;
    display: flex;
    flex-direction: column;
    align-items: center;
    text-align: center;
    box-shadow: 0 6px 22px rgba(0,0,0,0.18);
  }
  .label--cream {
    background: var(--cream);
    border: 1px solid var(--cream-edge);
    color: var(--ink-dark);
  }
  .label--black {
    background: var(--charcoal);
    border: 1px solid var(--charcoal-edge);
    color: var(--ink-light);
  }
  .brand-name {
    font-size: 34px;
    font-weight: 500;
    color: var(--wine-red);
    letter-spacing: 0.02em;
    line-height: 1;
  }
  .ship-art {
    width: 150px;
    height: 100px;
    margin: 18px 0 16px;
    display: block;
  }
  .variety {
    font-size: 34px;
    font-weight: 500;
    font-variant: small-caps;
    letter-spacing: 0.18em;
    line-height: 1;
  }
  .vintage {
    font-size: 17px;
    letter-spacing: 0.12em;
    margin-top: 6px;
  }
  .estate {
    font-size: 13px;
    font-variant: small-caps;
    letter-spacing: 0.16em;
    margin-top: 12px;
  }
  .region {
    font-size: 14px;
    font-variant: small-caps;
    letter-spacing: 0.1em;
    margin-top: auto;
  }
</style>
</head>
<body>
  <section class="label label--cream">
    <div class="brand-name">Marlow and Fenn</div>
    <svg class="ship-art" viewBox="0 0 150 100" role="img" aria-label="Pen sketch of a tall sailing ship at sea">
      <defs>
        <linearGradient id="sketch-cream" x1="0" y1="0" x2="0" y2="1">
          <stop offset="0" stop-color="#d8d0b4"/>
          <stop offset="1" stop-color="#b9b29c"/>
        </linearGradient>
      </defs>
      <rect width="150" height="100" rx="4" fill="url(#sketch-cream)"/>
    </svg>
    <div class="variety">Shiraz</div>
    <div class="vintage">2014</div>
    <div class="estate">Estate Grown</div>
    <div class="region">Ashbrook Clare Valley South Australia</div>
  </section>

  <section class="label label--black">
    <div class="brand-name">Marlow and Fenn</div>
    <svg class="ship-art" viewBox="0 0 150 100" role="img" aria-label="White line sketch of a tall sailing ship at sea">
      <defs>
        <linearGradient id="sketch-black" x1="0" y1="0" x2="0" y2="1">
          <stop offset="0" stop-color="#4a4a4a"/>
          <stop offset="1" stop-color="#333333"/>
        </linearGradient>
      </defs>
      <rect width="150" height="100" rx="4" fill="url(#sketch-black)"/>
    </svg>
    <div class="variety">Shiraz</div>
    <div class="vintage">2014</div>
    <div class="estate">Estate Grown</div>
    <div class="region">Ashbrook Clare Valley South Australia</div>
  </section>
</body>
</html>
```